New Business Card for Web Design/Internet Marketing Company

Looking for a great looking new business card. We are a 10 year old web design, internet marketing and website management company that works mostly with small businesses.

Our new card needs to better match the colors and style of our website, be bold, extremely usable and slightly edgy.

Target Market(s)

Small/Medium businesses that have websites

Industry/Entity Type

Internet

Requirements
Must have
• Front and back design, full color, rounded corners please

Must use the colors/style of our website (JPG provided)

INFO FOR CARDS (as readable as possible please)
Mark Lenner
President/CEO
mark@trelvanmedia.example
Phone: 520-381-7459
Toll Free: 866-381-7459
Address: 4315 W. Calloway Ave. Ste. 140, Tucson, AZ 85792

THINGS I WANT TO PROMOTE (if there is room):
1. Our Website - www.trelvanmedia.example

2. Social Media
Twitter: @trelvanmedia
Facebook: www.facebook.com/trelvanmedia

3. Our Services
Web Design
Internet Marketing
Website Management

```html
<!DOCTYPE html>
<html lang="en">
<head>
<meta charset="utf-8">
<title>Trelvan Media – Business Card</title>
<link href="https://fonts.googleapis.com/css2?family=Source+Sans+3:wght@400;600;700&display=swap" rel="stylesheet">
<style>
  :root {
    --orange: #f58634;
    --blue: #1a8fc9;
    --ink: #3d3d3d;
    --paper: #ffffff;
    --backdrop: #ececec;
    --rule: #b9b9b9;
  }
  * { margin: 0; padding: 0; box-sizing: border-box; }
  html, body {
    width: 1200px; height: 1003px; overflow: hidden;
    background: var(--backdrop);
    font-family: "Source Sans 3", "Myriad Pro", Arial, sans-serif;
  }
  .card {
    position: absolute;
    width: 719px; height: 410px;
    border-radius: 14px;
    overflow: hidden;
    box-shadow: 0 3px 10px rgba(0,0,0,.18);
  }
  /* Front */
  .card--front { left: 94px; top: 59px; background: var(--paper); }
  .brand {
    position: absolute; left: 0; right: 0; top: 72px;
    display: flex; justify-content: center; align-items: center; gap: 16px;
  }
  .brand__dot { width: 40px; height: 40px; border-radius: 50%; background: var(--orange); }
  .brand__name { font-size: 62px; font-weight: 700; color: var(--blue); letter-spacing: -0.5px; line-height: 1; }
  .rule-blue { position: absolute; left: 0; right: 0; top: 206px; height: 3px; background: var(--blue); }
  .name-band {
    position: absolute; left: 0; right: 0; top: 215px; height: 47px;
    background: var(--orange); color: #fff;
    display: flex; justify-content: center; align-items: center; gap: 8px;
  }
  .name-band__name { font-size: 27px; font-weight: 700; }
  .name-band__title { font-size: 21px; font-weight: 400; }
  .address {
    position: absolute; right: 377px; top: 312px;
    text-align: right; font-size: 18px; line-height: 25px; color: var(--ink);
    font-style: normal;
  }
  .divider { position: absolute; left: 362px; top: 283px; width: 2px; height: 109px; background: var(--rule); }
  .contacts { position: absolute; left: 384px; top: 286px; list-style: none; }
  .contacts li {
    display: flex; align-items: center; gap: 10px;
    font-size: 18px; line-height: 26px; color: var(--ink);
  }
  .contacts svg { width: 15px; height: 15px; fill: var(--ink); flex: none; }
  /* Back */
  .card--back { left: 393px; top: 520px; background: var(--orange); color: #fff; }
  .back-brand {
    position: absolute; left: 0; right: 0; top: 95px;
    display: flex; justify-content: center; align-items: center; gap: 20px;
  }
  .back-brand__dot { width: 56px; height: 56px; border-radius: 50%; background: #fff; }
  .back-brand__name { font-size: 84px; font-weight: 700; line-height: 1; }
  .services {
    position: absolute; left: 0; right: 0; top: 262px;
    text-align: center; font-size: 25px; font-weight: 700; line-height: 31px;
  }
  .services span::before { content: "● "; font-size: 18px; vertical-align: 2px; }
  .services span + span { margin-left: 16px; }
  .social {
    position: absolute; left: 0; right: 0; top: 340px;
    display: flex; justify-content: center; gap: 22px;
    font-size: 23px;
  }
  .social__item { display: flex; align-items: center; gap: 8px; }
  .social__box { width: 16px; height: 16px; background: #fff; border-radius: 2px; opacity: .85; }
</style>
</head>
<body>
  <section class="card card--front" aria-label="Business card front">
    <div class="brand">
      <span class="brand__dot"></span>
      <span class="brand__name">Trelvan Media</span>
    </div>
    <div class="rule-blue"></div>
    <div class="name-band">
      <span class="name-band__name">Mark Lenner ,</span>
      <span class="name-band__title">President/CEO</span>
    </div>
    <address class="address">
      4315 W. Calloway Ave. Ste. 140<br>
      Tucson, AZ 85792
    </address>
    <div class="divider"></div>
    <ul class="contacts">
      <li><svg viewBox="0 0 16 16"><path d="M4 1l3 3-1.6 2a9 9 0 0 0 4.6 4.6L12 9l3 3-2 3C7 15 1 9 1 3z"/></svg>866-381-7459</li>
      <li><svg viewBox="0 0 16 16"><path d="M4 1l3 3-1.6 2a9 9 0 0 0 4.6 4.6L12 9l3 3-2 3C7 15 1 9 1 3z"/></svg>520-381-7459</li>
      <li><svg viewBox="0 0 16 16"><path d="M1 6l7-4 7 4v8H1z M3 7l5 3 5-3" stroke="#fff" stroke-width="1"/></svg>mark@trelvanmedia.example</li>
      <li><svg viewBox="0 0 16 16"><circle cx="8" cy="8" r="7"/></svg>www.trelvanmedia.example</li>
    </ul>
  </section>

  <section class="card card--back" aria-label="Business card back">
    <div class="back-brand">
      <span class="back-brand__dot"></span>
      <span class="back-brand__name">Trelvan</span>
    </div>
    <p class="services">
      <span>Web Design</span><span>Internet Marketing</span><br>
      <span>Website Management</span>
    </p>
    <div class="social">
      <span class="social__item"><span class="social__box"></span>@trelvanmedia</span>
      <span class="social__item"><span class="social__box"></span>trelvanmedia</span>
    </div>
  </section>
</body>
</html>
```